Moxy Fen needs some awesome stationary

Do you have what it takes to get my brand? You either do or you don't, have a crack at a design and you my just win my business.

I don't want to waste your or my time, so put your creative genius on either a business card or envelope.

I however need a package of stationary that follows the same brand. I will message you to complete the remaining should I like your first submission.

Here is what I need, have a go!

Basically I need the following for my small business based in melbourne.
- Letterhead (printer ready and MS Word)
- Business Card
- Compliments Slip
- Envelope
- Proposal Cover Page (MS Word only)
- Presentation Folder
- Marbled Fox Cards
- Student Name Tent
- Index Cards
- Vell-Ka

I am establishing the brand and it must be modern, professional but also relaxed; that is not formal and not corporate. It represents a company are leaders, but small enough to care and operate like a bunch of friends. We are bringing people and conversations back to business, and turfing out all the bureaucracy and crazy and wasteful procedures. Its about "lets talk and figure it out together and find even better ways".

Target Market(s)

Mainly companies that build software products, but Agile practices are used in many other industries (even graphic design projects)

Industry/Entity Type

Information Technology

Font styles to use
Sans Serif

Colors
3176b5
aaaaaa

Requirements
Must have
• I like curves and circles and not boxes or rectangles.
• I want a colour rich design with my brand colours, but it must be balanced.
• I want more modern than traditional, but simple modern
Should not have
• Not corporate
• Please don't waste my time if your not going to think about it.
• Don't mess with my primary logo
• Don't change my colours
• Don't overlay logo on image

```html
<!DOCTYPE html>
<html lang="en">
<head>
<meta charset="utf-8">
<title>Moxy Fen — Business Card</title>
<link href="https://fonts.googleapis.com/css2?family=Open+Sans:wght@300;400;600;700&display=swap" rel="stylesheet">
<style>
  :root {
    --brand-blue: #3176b5;
    --card-blue: #2c5ea6;
    --deep-blue: #234d8c;
    --brand-grey: #aaaaaa;
    --band-grey: #9aa1ad;
    --paper: #ffffff;
    --stage: #e9ebef;
  }
  * { box-sizing: border-box; margin: 0; padding: 0; }
  html, body {
    width: 1200px; height: 950px; overflow: hidden;
    background: var(--stage);
    font-family: "Open Sans", Arial, sans-serif;
  }
  .canvas {
    position: relative; width: 1200px; height: 950px;
  }
  .card {
    position: absolute; left: 250px; width: 700px; height: 400px;
    border-radius: 26px; overflow: hidden;
    box-shadow: 0 10px 28px rgba(20, 40, 80, 0.18);
  }
  .card--front { top: 55px; background: var(--paper); }
  .card--back { top: 495px; background: var(--card-blue); }

  .card__shape { position: absolute; inset: 0; }

  .contact {
    position: absolute; left: 52px; top: 50px; color: var(--paper);
  }
  .contact__name {
    font-size: 28px; font-weight: 700; letter-spacing: 0.5px; text-transform: uppercase;
  }
  .contact__role { font-size: 19px; font-weight: 400; line-height: 1.3; }
  .contact__title { font-size: 19px; font-weight: 300; line-height: 1.3; }
  .contact__address {
    margin-top: 34px; font-size: 19px; font-weight: 300; line-height: 1.35; font-style: normal;
  }
  .contact__lines { margin-top: 26px; list-style: none; }
  .contact__lines li {
    display: flex; align-items: center; gap: 12px;
    font-size: 18px; font-weight: 300; line-height: 1.45;
  }
  .contact__icon { width: 18px; height: 18px; flex: none; }

  .brand {
    position: absolute; display: flex; align-items: center;
  }
  .brand__dot { border-radius: 50%; flex: none; }
  .brand__name { font-weight: 700; white-space: nowrap; }

  .brand--front {
    left: 470px; right: 10px; top: 110px;
    flex-direction: column; justify-content: center; gap: 18px;
  }
  .brand--front .brand__dot { width: 96px; height: 96px; background: var(--band-grey); }
  .brand--front .brand__name { font-size: 36px; color: var(--brand-blue); }

  .brand--back { left: 0; right: 0; top: 150px; justify-content: center; gap: 16px; }
  .brand--back .brand__dot { width: 70px; height: 70px; background: var(--paper); }
  .brand--back .brand__name { font-size: 56px; color: var(--paper); }

  .web-address {
    position: absolute; left: 0; right: 0; bottom: 40px; text-align: center;
    color: var(--paper); font-size: 17px; font-weight: 300; letter-spacing: 6px;
  }
</style>
</head>
<body>
<main class="canvas">

  <section class="card card--front" aria-label="Business card front">
    <svg class="card__shape" viewBox="0 0 700 400" preserveAspectRatio="none" aria-hidden="true">
      <path d="M0 0 H488 C438 130 438 270 498 400 H0 Z" fill="var(--band-grey)"/>
      <path d="M0 0 H470 C420 130 420 270 480 400 H0 Z" fill="var(--card-blue)"/>
      <path d="M0 0 H300 C240 140 250 280 330 400 H0 Z" fill="var(--brand-blue)" opacity="0.35"/>
    </svg>

    <div class="contact">
      <h1 class="contact__name">Dara Quill</h1>
      <p class="contact__role">CEO</p>
      <p class="contact__title">Professional Agile Trainer</p>
      <address class="contact__address">
        PO Box 4410<br>
        Larkmoor East<br>
        VIC 3199, Australia
      </address>
      <ul class="contact__lines">
        <li>
          <svg class="contact__icon" viewBox="0 0 24 24" aria-hidden="true"><path fill="#fff" d="M6.6 10.8a15 15 0 0 0 6.6 6.6l2.2-2.2c.3-.3.7-.4 1-.2 1.1.4 2.3.6 3.6.6.6 0 1 .4 1 1V20c0 .6-.4 1-1 1A17 17 0 0 1 3 4c0-.6.4-1 1-1h3.5c.6 0 1 .4 1 1 0 1.3.2 2.5.6 3.6.1.3 0 .7-.2 1z"/></svg>
          1300 669 934
        </li>
        <li>
          <svg class="contact__icon" viewBox="0 0 24 24" aria-hidden="true"><rect x="6" y="2" width="12" height="20" rx="2" fill="none" stroke="#fff" stroke-width="2"/><circle cx="12" cy="18" r="1.2" fill="#fff"/></svg>
          +61 400 555 018
        </li>
        <li>
          <svg class="contact__icon" viewBox="0 0 24 24" aria-hidden="true"><rect x="2" y="5" width="20" height="14" rx="1.5" fill="#fff"/><path d="M3 6l9 7 9-7" fill="none" stroke="var(--card-blue)" stroke-width="1.8"/></svg>
          dara@moxy-fen.com.au
        </li>
        <li>
          <svg class="contact__icon" viewBox="0 0 24 24" aria-hidden="true"><circle cx="12" cy="12" r="10" fill="#fff"/><path d="M2 12h20M12 2c3 3 3 17 0 20M12 2c-3 3-3 17 0 20" fill="none" stroke="var(--card-blue)" stroke-width="1.5"/></svg>
          www.moxy-fen.com.au
        </li>
      </ul>
    </div>

    <div class="brand brand--front">
      <span class="brand__dot" aria-hidden="true"></span>
      <span class="brand__name">Moxy Fen</span>
    </div>
  </section>

  <section class="card card--back" aria-label="Business card back">
    <div class="brand brand--back">
      <span class="brand__dot" aria-hidden="true"></span>
      <span class="brand__name">Moxy Fen</span>
    </div>
    <p class="web-address">www.moxy-fen.com.au</p>
  </section>

</main>
</body>
</html>
```